Business Card: RW Office Partners - Your organised problem solver

Business Name: RW Office Partners
Website: www.rwofficepartners.com.au
Email: marisol@rwofficepartners.com.au
Mobile: 61 482 907 236
Facebook: @rwofficepartners
Instrgram: @rwofficepartners

Brading Colours:
HEX
#986474
#ddccd3
#7a8498
#c9d8e4
#000000
#ffffff

Tag Line: Your organised problem solver

Link to DRAFT website:
https://deskhelpcollective.wixsite.com/rw-office-partners

About Page from the website:
My name is Marisol Wrenfield, and I would love to assist you to become more productive in your day to day and achieve your business and personal goals.
My mission is to give you time, time to work on the important tasks of your business or to be able to spend more time with your family. I will take on the tasks you don’t have time for, don’t know well or simply don’t like to do.
I have an extensive background in Administration, Tender Coordination, Document Control, WHS and Quality Management working primarily in the Construction, Mining and Corporate World.
I am passionate about being organised, having order and making things in your life (and mine) easier! I love to watch something unfold and grow into something amazing! I am known for being the go-to problem solver, the organiser of all things, producing high standards of work even under pressure. I’m also a confident communicator, and I understand that you’re busy running your business.

Target Market(s)

Small to Medium Business who require assistance in their business by a virtual assistant.

Industry/Entity Type

Virtual Assistant

Contact Information for Business Card

Mobile: 61 482 907 236

Font styles to use
Sans Serif

Colors
ffffff

Requirements
Must have
• Branding Colours as outlined.
Contact Details as outlined.
Logo as provided.
Proper contact details - mobile, facebook, instragm, website.
Simple, Elegant, very clean looking.
Should not have
• Note cute with pictures.
Not too girly as still want to market to construction companies.

```html
<!DOCTYPE html>
<html lang="en">
<head>
<meta charset="utf-8">
<title>RW Office Partners – Business Card</title>
<link rel="stylesheet" href="https://fonts.googleapis.com/css2?family=Roboto:ital,wght@0,400;0,500;0,700;1,400&display=swap">
<style>
  :root {
    --backdrop: #3b3a3d;
    --card: #1d1b1f;
    --mauve: #986474;
    --mauve-light: #ddccd3;
    --slate: #7a8498;
    --emboss: #545158;
    --muted: #5b5860;
    --white: #ffffff;
  }
  * { box-sizing: border-box; margin: 0; padding: 0; }
  html, body {
    width: 799px;
    height: 1200px;
    overflow: hidden;
  }
  body {
    background: var(--backdrop);
    font-family: "Roboto", Arial, sans-serif;
    color: var(--white);
    position: relative;
  }
  .card {
    position: absolute;
    left: 80px;
    width: 640px;
    height: 391px;
    background: var(--card);
    border-radius: 4px;
    box-shadow: 0 14px 30px rgba(0,0,0,.45);
  }
  .card--front { top: 150px; }
  .card--back { top: 665px; }

  /* Front */
  .front-brand {
    position: absolute;
    left: 70px;
    top: 120px;
    display: flex;
    align-items: center;
    gap: 18px;
  }
  .front-brand__mark {
    width: 62px;
    height: 62px;
    background: var(--emboss);
  }
  .front-brand__name {
    font-size: 44px;
    font-weight: 500;
    letter-spacing: 1px;
    color: var(--emboss);
    text-transform: uppercase;
    line-height: 1;
  }
  .front-socials {
    position: absolute;
    left: 0;
    right: 0;
    top: 262px;
    display: flex;
    justify-content: center;
    gap: 26px;
    font-size: 17px;
  }
  .social {
    display: flex;
    align-items: center;
    gap: 9px;
  }
  .social__dot {
    width: 14px;
    height: 14px;
    border-radius: 3px;
    background: var(--mauve);
    flex: none;
  }

  /* Back */
  .back-brand {
    position: absolute;
    left: 42px;
    top: 140px;
    width: 270px;
  }
  .back-brand__name {
    font-size: 27px;
    font-weight: 500;
    color: var(--mauve);
    text-transform: uppercase;
    line-height: 1.1;
  }
  .back-brand__tagline {
    margin-top: 8px;
    font-size: 15px;
    font-style: italic;
    color: var(--muted);
  }
  .contact {
    position: absolute;
    left: 345px;
    top: 120px;
  }
  .contact__name {
    font-size: 22px;
    font-weight: 700;
    color: var(--mauve);
  }
  .contact__role {
    margin-top: 4px;
    font-size: 15px;
  }
  .contact__list {
    list-style: none;
    margin-top: 18px;
    font-size: 14.5px;
    line-height: 23px;
  }
  .contact__list li {
    display: flex;
    align-items: center;
    gap: 12px;
  }
  .contact__icon {
    width: 14px;
    height: 14px;
    flex: none;
    fill: var(--mauve);
  }
</style>
</head>
<body>
  <section class="card card--front" aria-label="Card front">
    <div class="front-brand">
      <span class="front-brand__mark"></span>
      <span class="front-brand__name">RW Office Partners</span>
    </div>
    <div class="front-socials">
      <span class="social"><span class="social__dot"></span>@rwofficepartners</span>
      <span class="social"><span class="social__dot"></span>@rwofficepartners</span>
    </div>
  </section>

  <section class="card card--back" aria-label="Card back">
    <div class="back-brand">
      <p class="back-brand__name">RW Office Partners</p>
      <p class="back-brand__tagline">Your organised problem solver</p>
    </div>
    <div class="contact">
      <p class="contact__name">Marisol Wrenfield</p>
      <p class="contact__role">Virtual Assistant</p>
      <ul class="contact__list">
        <li>
          <svg class="contact__icon" viewBox="0 0 16 16" aria-hidden="true"><path d="M3 1h3l1.5 4-2 1.3a9 9 0 0 0 4.2 4.2L11 8.5l4 1.5v3a2 2 0 0 1-2 2A12 12 0 0 1 1 3a2 2 0 0 1 2-2z"/></svg>
          61 482 907 236
        </li>
        <li>
          <svg class="contact__icon" viewBox="0 0 16 16" aria-hidden="true"><path d="M1 3h14v10H1z M1 3l7 6 7-6" fill="none" stroke="#986474" stroke-width="1.6"/></svg>
          marisol@rwofficepartners.com.au
        </li>
        <li>
          <svg class="contact__icon" viewBox="0 0 16 16" aria-hidden="true"><g fill="none" stroke="#986474" stroke-width="1.4"><circle cx="8" cy="8" r="6.5"/><ellipse cx="8" cy="8" rx="3" ry="6.5"/><path d="M1.5 8h13"/></g></svg>
          www.rwofficepartners.com.au
        </li>
        <li><span class="social__dot"></span>@rwofficepartners</li>
        <li><span class="social__dot"></span>@rwofficepartners</li>
      </ul>
    </div>
  </section>
</body>
</html>
```